8x8 Social Media Ad - Brant Summit Expo

Attention Real Estate Agents
Please join us for our
Quarterly Real Estate Training Expo
The 2nd Saturday of February, May, August and November
Our Next Training Expo is _________________________________
From 9 am to 1 pm
at
Halvorne Suites Millbrook Court
4817 Copper Willow Lane, Dunmere, MD 20588
Scheduled Speakers
9:00 am - Marcus Pellington - Orientation
9:30 am - Derrin Oakfield - Multiple Income Streams / Crest Program
10:00 am - Talia Brennick - Marketing though Social Media
10:45 am - Rex Dunmore - Generating Business through Ru-Plaza
11:30 am - Kemi Adeyoro - Real Estate Investing
12:15 pm - Gregor Tamsey - (Main Speaker) Training Topic TBA
For more information call Marcus Pellington at (240) 555-0183 or email mpellington@brantsummithomes.example

```html
<!DOCTYPE html>
<html lang="en">
<head>
<meta charset="utf-8">
<title>Brant Summit Expo – Quarterly Real Estate Training Expo</title>
<link href="https://fonts.googleapis.com/css2?family=Lato:ital,wght@0,400;0,700;0,900;1,400;1,700&display=swap" rel="stylesheet">
<style>
  :root{
    --navy:#0c1a26;
    --navy-deep:#07121b;
    --teal-dark:#123848;
    --cyan:#1fc3dd;
    --cyan-glow:rgba(45,215,240,.75);
    --red:#e3202a;
    --white:#ffffff;
    --photo:#5a6670;
  }
  *{margin:0;padding:0;box-sizing:border-box}
  html,body{width:1200px;height:1200px;overflow:hidden}
  body{font-family:"Lato",sans-serif;color:var(--white);background:var(--navy)}
  .ad{position:relative;width:1200px;height:1200px;overflow:hidden}
  .ad__backdrop{position:absolute;inset:0;
    background:
      linear-gradient(180deg,rgba(7,18,27,.35) 0%,rgba(7,18,27,.55) 60%,rgba(7,18,27,.85) 100%),
      linear-gradient(115deg,var(--navy-deep) 0%,var(--teal-dark) 45%,#1b3e4f 70%,var(--navy) 100%);}
  .brand{position:absolute;left:44px;top:62px;display:flex;align-items:center;gap:12px}
  .brand__mark{width:26px;height:26px;background:var(--cyan)}
  .brand__name{font-weight:900;font-size:28px;color:var(--cyan);line-height:1.05;width:150px}
  .headline{position:absolute;left:0;right:0;text-align:center}
  .headline--attention{top:84px;font-size:56px;font-weight:700;color:var(--red);letter-spacing:8px}
  .headline--audience{top:155px;font-size:64px;font-weight:900;color:var(--cyan)}
  .headline--invite{top:244px;font-size:37px;font-weight:400}
  .headline--event{top:297px;font-size:37px;font-weight:900;color:var(--cyan)}
  .details{position:absolute;left:75px;top:371px;width:1040px;height:309px;border:3px solid var(--cyan);
    border-radius:24px;box-shadow:0 0 16px var(--cyan-glow),inset 0 0 14px var(--cyan-glow);
    background:rgba(7,18,27,.25);text-align:center;padding-top:27px;font-size:30px;font-weight:700;line-height:41.6px}
  .details__blank{display:inline-block;width:345px;border-bottom:2px solid var(--white);height:30px;vertical-align:baseline}
  .speakers__title{position:absolute;left:0;right:0;top:716px;text-align:center;font-size:24px;font-weight:700;
    color:var(--cyan);letter-spacing:12px}
  .timeline{position:absolute;left:75px;top:783px;width:1040px;height:2px;background:var(--cyan)}
  .speakers{position:absolute;left:40px;top:776px;display:flex;width:1110px}
  .speaker{width:185px;display:flex;flex-direction:column;align-items:center;text-align:center}
  .speaker__dot{width:14px;height:14px;border-radius:50%;background:var(--cyan)}
  .speaker__time{margin-top:27px;font-size:18px;font-weight:900;color:var(--cyan)}
  .speaker__photo{margin-top:12px;width:166px;height:166px;border-radius:50%;border:3px solid var(--cyan);
    background:radial-gradient(circle at 50% 40%,#8a9096 0%,var(--photo) 55%,#2c3338 100%)}
  .speaker__name{margin-top:16px;font-size:17px;font-weight:900;color:var(--cyan);text-transform:uppercase;white-space:nowrap}
  .speaker__topic{font-size:16.5px;font-style:italic;font-weight:700;line-height:22px;padding:0 14px}
  .contact{position:absolute;left:0;right:0;top:1146px;text-align:center;font-size:18.5px;color:var(--cyan)}
</style>
</head>
<body>
<main class="ad">
  <div class="ad__backdrop" role="img" aria-label="Dusky city skyline of glass office towers"></div>

  <div class="brand"><span class="brand__mark"></span><span class="brand__name">Brant Summit Expo</span></div>

  <h1 class="headline headline--attention">ATTENTION!</h1>
  <h2 class="headline headline--audience">REAL ESTATE AGENTS</h2>
  <p class="headline headline--invite">PLEASE JOIN US FOR OUR</p>
  <p class="headline headline--event">QUARTERLY REAL ESTATE TRAINING EXPO</p>

  <section class="details">
    <p>The 2nd Saturday of February, May, August and November</p>
    <p>Our Next Training Expo is <span class="details__blank"></span></p>
    <p>From 9 am to 1 pm</p>
    <p>at</p>
    <p>Halvorne Suites Millbrook Court</p>
    <p>4817 Copper Willow Lane, Dunmere, MD 20588</p>
  </section>

  <h3 class="speakers__title">SCHEDULED SPEAKERS</h3>
  <div class="timeline"></div>
  <section class="speakers">
    <article class="speaker"><span class="speaker__dot"></span><span class="speaker__time">09:00AM</span>
      <div class="speaker__photo" role="img" aria-label="Portrait photo of Marcus Pellington"></div>
      <span class="speaker__name">Marcus Pellington</span><span class="speaker__topic">Orientation</span></article>
    <article class="speaker"><span class="speaker__dot"></span><span class="speaker__time">09:30AM</span>
      <div class="speaker__photo" role="img" aria-label="Portrait photo of Derrin Oakfield"></div>
      <span class="speaker__name">Derrin Oakfield</span><span class="speaker__topic">Multiple Income Streams / Crest Program</span></article>
    <article class="speaker"><span class="speaker__dot"></span><span class="speaker__time">10:00AM</span>
      <div class="speaker__photo" role="img" aria-label="Portrait photo of Talia Brennick"></div>
      <span class="speaker__name">Talia Brennick</span><span class="speaker__topic">Marketing through Social Media</span></article>
    <article class="speaker"><span class="speaker__dot"></span><span class="speaker__time">10:45AM</span>
      <div class="speaker__photo" role="img" aria-label="Portrait photo of Rex Dunmore"></div>
      <span class="speaker__name">Rex Dunmore</span><span class="speaker__topic">Generating Business through Ru-Plaza</span></article>
    <article class="speaker"><span class="speaker__dot"></span><span class="speaker__time">11:30AM</span>
      <div class="speaker__photo" role="img" aria-label="Portrait photo of Kemi Adeyoro"></div>
      <span class="speaker__name">Kemi Adeyoro</span><span class="speaker__topic">Real Estate Investing</span></article>
    <article class="speaker"><span class="speaker__dot"></span><span class="speaker__time">12:15PM</span>
      <div class="speaker__photo" role="img" aria-label="Portrait photo of Gregor Tamsey"></div>
      <span class="speaker__name">Gregor Tamsey</span><span class="speaker__topic">(Main Speaker) Training Topic TBA</span></article>
  </section>

  <p class="contact">For more information call Marcus Pellington at (240) 555-0183 or email mpellington@brantsummithomes.example</p>
</main>
</body>
</html>
```